Simple Business Card Design for Tavlo

Job:

Make a very simple, minimalist business card design with my details including adjusted logo. One side to be white (with logo & text). Other side to be yellow - try plain or with logo (or part of logo eg Z). Need business card to have continuity with website.

Logo:
Our logo is made from a free download font website:
http://www.typewell.net/search.php?q=rubber
but the spacing/kerning needs correcting/adjusting as the font spaces unevenly between letters (see attached files). Need logo to be very crisp/sharp when printed.

Printing:
We will be using Plika.com so the design needs to conform to their requirements, see here:

http://uk.plika.com/products/luxe/business-cards.html (scroll down for dimensions and guidelines)

Design:

must say "plant-based food consulting" underneath logo or somewhere
no address needed in contact section
sharp corners (not rounded)
one side white, one side yellow

name: Rosalind Whitcombe
1xmobile number: +44 7700900463
1xtwiiter: @brimcounsel
website address www.orchardtable.com
email address brim@orchardtable.com

Should be easy quick job, prompt + detailed feedback given, am online in UK 9am-10pm for next 3 days. Website is www.orchardtable.com

Industry/Entity Type

Business

Requirements
Must have
• The logo must be corrected. The kerning is not right.

Please use a warm-grey for text

Please submit in matt format, we will be printing matt finish.

Should not have
• Avoid using banners or curvy highlights

Please avoid using black

Please avoid submitting in gloss finish

```html
<!DOCTYPE html>
<html lang="en">
<head>
<meta charset="utf-8">
<title>BRIM – Business Card</title>
<link rel="stylesheet" href="https://fonts.googleapis.com/css2?family=Questrial&family=Montserrat:wght@700&display=swap">
<style>
  :root {
    --backdrop: #e9e8e5;
    --card: #f7f7f5;
    --band: #403f3f;
    --brand-yellow: #e6e52c;
    --warm-grey: #4b4847;
    --tagline: #f2f2f0;
    --icon-glyph: #e6e52c;
  }
  * { box-sizing: border-box; margin: 0; padding: 0; }
  html, body {
    width: 1200px; height: 900px; overflow: hidden;
    background: var(--backdrop);
  }
  .canvas { position: relative; width: 1200px; height: 900px; }
  .business-card {
    position: absolute; left: 100px; top: 165px;
    width: 1000px; height: 570px;
    background: var(--card);
    box-shadow: 0 2px 10px rgba(0,0,0,0.08);
    font-family: "Questrial", "Century Gothic", sans-serif;
    color: var(--warm-grey);
    overflow: hidden;
  }
  .brand-band {
    position: absolute; left: 0; top: 42px;
    width: 100%; height: 205px;
    background: var(--band);
  }
  .brand-name {
    position: absolute; left: 58px; top: 18px;
    font-size: 150px; line-height: 1;
    letter-spacing: 6px;
    color: var(--brand-yellow);
  }
  .tagline {
    position: absolute; right: 40px; bottom: 22px;
    font-size: 27px; color: var(--tagline);
  }
  .contact-list {
    position: absolute; left: 58px; top: 318px;
    list-style: none;
  }
  .contact-item {
    display: flex; align-items: center; gap: 22px;
    height: 40px; font-size: 26px; white-space: nowrap;
  }
  .contact-icon { width: 26px; height: 26px; flex: none; }
  .person {
    position: absolute; right: 40px; bottom: 58px; text-align: right;
  }
  .person-name {
    font-family: "Montserrat", "Century Gothic", sans-serif;
    font-weight: 700; font-size: 32px; letter-spacing: 1px;
    white-space: nowrap;
  }
  .person-role { font-size: 28px; margin-top: 2px; }
</style>
</head>
<body>
<main class="canvas">
  <article class="business-card">
    <header class="brand-band">
      <div class="brand-name">BRIM</div>
      <p class="tagline">Plant-based food consulting</p>
    </header>

    <ul class="contact-list">
      <li class="contact-item">
        <svg class="contact-icon" viewBox="0 0 26 26" aria-hidden="true">
          <rect width="26" height="26" rx="5" fill="var(--band)"/>
          <rect x="8" y="5" width="10" height="16" rx="2" fill="none" stroke="var(--icon-glyph)" stroke-width="2"/>
          <circle cx="13" cy="18" r="1" fill="var(--icon-glyph)"/>
        </svg>
        <span>+44 7700 900463</span>
      </li>
      <li class="contact-item">
        <svg class="contact-icon" viewBox="0 0 26 26" aria-hidden="true">
          <rect width="26" height="26" rx="5" fill="var(--band)"/>
          <path d="M5 6 H21 V16 H12 L8 20 V16 H5 Z" fill="var(--icon-glyph)"/>
        </svg>
        <span>@brimcounsel</span>
      </li>
      <li class="contact-item">
        <svg class="contact-icon" viewBox="0 0 26 26" aria-hidden="true">
          <rect width="26" height="26" rx="5" fill="var(--band)"/>
          <rect x="5" y="7" width="16" height="12" fill="var(--icon-glyph)"/>
          <path d="M5 7 L13 14 L21 7 M5 19 L11 13 M21 19 L15 13" fill="none" stroke="var(--band)" stroke-width="1.4"/>
        </svg>
        <span>brim@orchardtable.com</span>
      </li>
      <li class="contact-item">
        <svg class="contact-icon" viewBox="0 0 26 26" aria-hidden="true">
          <rect width="26" height="26" rx="5" fill="var(--band)"/>
          <g fill="none" stroke="var(--icon-glyph)" stroke-width="1.5">
            <circle cx="13" cy="13" r="8"/>
            <ellipse cx="13" cy="13" rx="3.5" ry="8"/>
            <path d="M5 13 H21 M6.5 9 H19.5 M6.5 17 H19.5"/>
          </g>
        </svg>
        <span>www.orchardtable.com</span>
      </li>
    </ul>

    <section class="person">
      <h1 class="person-name">ROSALIND WHITCOMBE</h1>
      <p class="person-role">General Manager</p>
    </section>
  </article>
</main>
</body>
</html>
```